Business Card Design

New business card design

Target Market(s)

Residential & Commercial Property Managers

Industry/Entity Type

Plumbing Services

Contact Information for Business Card

Name - Rowan Keddle, title - Director, Phone Number - 0431 286 517, email - rowan@tbk-plumbing.com.au, Company ABN - 73 215 904 386,

Font styles to use
Sans Serif

Colors
0054AA
0677BA
7BADD7
CADEEF
E8F1F8

```html
<!DOCTYPE html>
<html lang="en">
<head>
<meta charset="utf-8">
<title>TBK Plumbing Services – Business Card</title>
<link rel="stylesheet" href="https://fonts.googleapis.com/css2?family=Poppins:wght@300;400;500;600&display=swap">
<style>
  :root {
    --stage: #222222;
    --card-dark: #1b2028;
    --brand-blue: #1e9fdc;
    --blue-deep: #0677BA;
    --blue-soft: #7BADD7;
    --ink-white: #ffffff;
    --ink-grey: #7d776f;
  }
  * { box-sizing: border-box; margin: 0; padding: 0; }
  html, body {
    width: 1200px; height: 780px; overflow: hidden;
    background: var(--stage);
    font-family: "Poppins", sans-serif;
  }
  .canvas {
    position: relative; width: 1200px; height: 780px;
    display: flex; align-items: center; justify-content: center; gap: 50px;
  }
  .card {
    position: relative; width: 520px; height: 318px;
    border-radius: 22px; overflow: hidden;
    box-shadow: 0 14px 30px rgba(0,0,0,0.45);
  }
  .card-front { background: var(--card-dark); }
  .card-back {
    background: linear-gradient(135deg, var(--blue-deep) 0%, var(--brand-blue) 50%, var(--blue-soft) 100%);
  }

  .company-name {
    position: absolute; left: 44px; top: 86px; width: 200px;
    font-size: 26px; font-weight: 500; line-height: 1.2;
    color: var(--ink-white);
  }

  .divider { position: absolute; left: 0; top: 0; }

  .abn {
    position: absolute; left: 44px; bottom: 38px;
    font-size: 13px; font-weight: 400; color: var(--brand-blue);
  }

  .contact-block { position: absolute; left: 300px; top: 80px; }
  .person-name { font-size: 26px; line-height: 1.1; white-space: nowrap; }
  .first-name { font-weight: 600; color: var(--brand-blue); }
  .last-name { font-weight: 300; color: var(--ink-grey); }
  .person-title {
    font-size: 13px; font-weight: 500; color: var(--ink-white);
    margin-top: 3px;
  }
  .contact-list { list-style: none; margin-top: 20px; }
  .contact-item {
    display: flex; align-items: center; gap: 8px;
    font-size: 12.5px; font-weight: 400; color: var(--ink-white);
    margin-bottom: 8px; white-space: nowrap;
  }
  .contact-icon { width: 13px; height: 13px; flex: none; }
</style>
</head>
<body>
<main class="canvas">

  <section class="card card-front" aria-label="Business card front">
    <p class="company-name">TBK Plumbing Services</p>

    <svg class="divider" width="520" height="318" aria-hidden="true">
      <line x1="298" y1="42" x2="246" y2="290" stroke="var(--brand-blue)" stroke-width="0.9"/>
    </svg>

    <div class="contact-block">
      <p class="person-name"><span class="first-name">Rowan</span> <span class="last-name">Keddle</span></p>
      <p class="person-title">Director</p>
      <ul class="contact-list">
        <li class="contact-item">
          <svg class="contact-icon" viewBox="0 0 24 24" aria-hidden="true"><path fill="var(--brand-blue)" d="M6.6 10.8a15.2 15.2 0 0 0 6.6 6.6l2.2-2.2a1 1 0 0 1 1-.25 11.4 11.4 0 0 0 3.6.57 1 1 0 0 1 1 1V20a1 1 0 0 1-1 1A17 17 0 0 1 3 4a1 1 0 0 1 1-1h3.5a1 1 0 0 1 1 1c0 1.25.2 2.45.57 3.57a1 1 0 0 1-.25 1z"/></svg>
          0431 286 517
        </li>
        <li class="contact-item">
          <svg class="contact-icon" viewBox="0 0 24 24" aria-hidden="true"><rect x="2" y="5" width="20" height="14" rx="2" fill="var(--brand-blue)"/><path d="M3 6l9 7 9-7" fill="none" stroke="var(--card-dark)" stroke-width="1.6"/></svg>
          rowan@tbk-plumbing.com.au
        </li>
        <li class="contact-item">
          <svg class="contact-icon" viewBox="0 0 24 24" aria-hidden="true"><circle cx="12" cy="12" r="10" fill="var(--brand-blue)"/><path d="M2 12h20M12 2c3 3 3 17 0 20M12 2c-3 3-3 17 0 20" fill="none" stroke="var(--card-dark)" stroke-width="1.3"/></svg>
          www.tbk-plumbing.com.au
        </li>
      </ul>
    </div>

    <p class="abn">ABN - 73 215 904 386,</p>
  </section>

  <section class="card card-back" role="img" aria-label="Card reverse: repeating water-drop pattern in bright blue tones"></section>

</main>
</body>
</html>
```